Around the world sailing blogger needs a book cover template designed

Hello. I'm interested in writing a series of 'guides' in relation to sailing and live-aboard cruising. Last April my husband and I sold all our possessions and purchased the largest boat we could find. Since then I've been sailing and blogging about our experiences and am slowing building up a popular website and shop. The first guide in my series is finished. It's a guide to using the VHF radio with checklist templates for the user to use. The next guide might have something to do with maintenance checklists (engine, generator, water maker, etc). Anyway, I need a cover that will act as a template for future guides so it needs to have nautical imagery, a headline, subhead, author, my logo and perhaps a quote or something and it needs to be replicated across the series. In other words it needs to be created in a way that we (or should I say you) can make more covers easily with the same look and feel. The cover needs to be created for PDF, Plume (electronic) PressNook (hardcopy) at the very least... And I'll also need some thumbnails for promotional purposes. The imagery on this first one needs to cover communication/VHF radio/Sailing... I know it sounds like a boring book but it will be very useful to the user. And I really need the cover to look awesome :) To see my website it's at DriftwoodKestrel.com. Final note - I've never used Pixel Harbor before so this is my first time. I'm not sure if I've given you everything you need...Also, I need more than just a cover. Hopefully I can find someone that can help me with all my books and digital products that I have lined up. I'll stop typing now :)

I've just added of some pictures of our boat while we're sailing it. They might make a nice cover - I don't know. I'm really sorry for not providing this to begin with... I've never used this service before so I'm trialling it to see if it's better/easier than Gigvane. I know it's really frustrating when someone wants something and doesn't give all the information up front. I just didn't understand how this all works so I apologise. I have thousands of photos...these were taken by a professional so I'm hoping they're the best... Also, keep in mind I'm looking for a series of guides and this one is on VHF radio...I can't have a photo of our boat for every guide. Next time I post a project I'll be far more knowledgable. Sorry for any inconvenience. That being said, if we do use a photo of the back of the boat, the logo is already there so we don't need the logo twice... Liv

Target Market(s)

Sailors, boaters, full time boaters...sailors sailing around the world. Anyone that owns a boat and a VHF radio. Both men and women... English speaking. Biggest audience in USA then UK, Australian, NZ, Europe..

Industry/Entity Type

Building

Font styles to use
Serif
Sans Serif

Requirements
Must have
• My logo, headlines, subhead, author line and good imagery. Using a VHF is rather boring but my book offers templates so that users can easily fill out a MAYDAY (SOS) form and feel confident when they have to broadcast the information across the radio. It an idiots guide to VHF radios...A lot of people are nervous about using them when they first start out - especially women - so this guide will help reduce anxiety.
Nice to have
• Colours that match my website might be too much blue - might be nice to have some different colors?

```html
<!DOCTYPE html>
<html lang="en">
<head>
<meta charset="utf-8">
<title>VHF Radio Checklists and Templates for Sailors — Front and Back Cover</title>
<link rel="stylesheet" href="https://fonts.googleapis.com/css2?family=Oswald:wght@500;700&family=Open+Sans:wght@400;600&display=swap">
<style>
  :root {
    --page-bg: #eceeef;
    --sky-top: #3d86c8;
    --sky-mid: #7fb8e3;
    --sky-haze: #c4def2;
    --sea-mid: #2a6fb0;
    --sea-deep: #10467f;
    --slate: #566671;
    --white: #ffffff;
    --gold: #d9aa4a;
    --radio-light: #dde4ea;
    --radio-dark: #7d8a96;
  }
  * { margin: 0; padding: 0; box-sizing: border-box; }
  html, body { width: 1200px; height: 1200px; overflow: hidden; }
  body {
    background: var(--page-bg);
    display: flex;
    align-items: center;
    justify-content: center;
    gap: 40px;
  }
  .cover {
    position: relative;
    width: 540px;
    height: 700px;
    overflow: hidden;
    box-shadow: 0 10px 28px rgba(0,0,0,.18);
  }

  /* Photo placeholders */
  .photo-sea {
    position: absolute; inset: 0;
    background: linear-gradient(180deg,
      var(--sky-top) 0%, var(--sky-mid) 50%, var(--sky-haze) 60%,
      var(--sea-mid) 64%, var(--sea-deep) 100%);
  }
  .photo-strip {
    position: absolute; left: 0; top: 0; width: 100%; height: 150px;
    background: linear-gradient(180deg,
      var(--sky-top) 0%, var(--sky-mid) 60%, var(--sky-haze) 82%,
      var(--sea-mid) 86%, var(--sea-deep) 100%);
  }

  /* Brand (invented name, no mark) */
  .brand {
    position: absolute;
    display: flex; align-items: center; gap: 10px;
  }
  .brand-circle {
    width: 40px; height: 40px; border-radius: 50%;
    border: 2px solid var(--white);
  }
  .brand-name {
    font-family: "Oswald", sans-serif; font-weight: 500;
    font-size: 16px; letter-spacing: 1.5px;
    color: var(--white); text-transform: uppercase;
  }

  /* Front cover */
  .front .brand { left: 28px; top: 28px; }
  .front .band-left {
    position: absolute; left: 0; top: 210px; width: 190px; height: 70px;
    background: var(--slate);
  }
  .front .title-panel {
    position: absolute; left: 190px; top: 90px; right: 0; height: 190px;
    background: var(--slate);
    padding: 24px 0 0 24px;
  }
  .front .title {
    width: 200px;
    font-family: "Oswald", sans-serif; font-weight: 700;
    font-size: 30px; line-height: 35px;
    color: var(--white); text-transform: uppercase;
  }
  .front .radio-photo {
    position: absolute; right: 16px; top: 44px;
    width: 100px; height: 100px; border-radius: 50%;
    border: 4px solid var(--white);
    background: radial-gradient(circle at 50% 45%, var(--radio-light) 0%, #c3ccd4 55%, var(--radio-dark) 100%);
    box-shadow: 0 3px 8px rgba(0,0,0,.2);
  }
  .front .subtitle {
    position: absolute; right: 24px; top: 318px; width: 300px;
    font-family: "Oswald", sans-serif; font-weight: 700;
    font-size: 23px; line-height: 29px;
    color: var(--gold); text-align: right;
  }
  .front .author {
    position: absolute; right: 24px; top: 470px;
    font-family: "Oswald", sans-serif; font-weight: 500;
    font-size: 22px; letter-spacing: 1.5px;
    color: var(--white); text-transform: uppercase;
  }

  /* Back cover */
  .back { background: var(--slate); }
  .back .brand {
    right: 22px; top: 168px;
    flex-direction: column; gap: 6px; width: 120px;
  }
  .back .brand-name { font-size: 11px; letter-spacing: 1px; text-align: center; }
  .back .rule {
    position: absolute; left: 30px; width: 340px; height: 2px;
    background: var(--white);
  }
  .back .rule-top { top: 172px; }
  .back .rule-bottom { top: 652px; }
  .back .heading {
    position: absolute; left: 30px; top: 184px; width: 340px;
    font-family: "Oswald", sans-serif; font-weight: 700;
    font-size: 19px; line-height: 24px;
    color: var(--white); text-align: center;
  }
  .back .blurb {
    position: absolute; left: 30px; top: 246px; width: 340px;
    font-family: "Open Sans", sans-serif; font-weight: 400;
    font-size: 10.5px; line-height: 15.5px;
    color: var(--white);
  }
  .back .blurb p + p { margin-top: 6px; }
  .back .side-column {
    position: absolute; left: 398px; top: 246px; width: 120px;
    font-family: "Open Sans", sans-serif; font-weight: 400;
    font-size: 10px; line-height: 15px;
    color: var(--white); text-align: justify;
  }
</style>
</head>
<body>
  <section class="cover back">
    <div class="photo-strip" role="img" aria-label="Photograph of a white sailing yacht on the open sea under a blue sky with white clouds"></div>

    <div class="brand">
      <span class="brand-circle"></span>
      <span class="brand-name">Driftwood Kestrel</span>
    </div>

    <div class="rule rule-top"></div>
    <h2 class="heading">Reducing Mistakes &amp; Making It Easier<br>When Speaking Over The VHF Radio</h2>

    <div class="blurb">
      <p>I've just added of some pictures of our boat while we're sailing it. They might make a nice cover - I don't know. I'm really sorry for not providing this to begin with... I've never used this service before so I'm trialling it to see if it's better/easier than Gigvane. I know it's really frustrating when someone wants something and doesn't give all the information up front. I just didn't understand how this all works so I apologise. I have thousands of photos...these were taken by a professional so I'm hoping they're the best... Also, keep in mind I'm looking for a series of guides and this one is on VHF radio...I can't have a photo of our boat for every guide. Next time I post a project I'll be far more knowledgable. Sorry for any inconvenience. That being said, if we do use a photo of the back of the boat, the logo is already there so we don't need the logo twice... Liv</p>
      <p>Added Sunday, January 11, 2015</p>
      <p>Target Market(s)<br>Sailors, boaters, full time boaters...sailors sailing around the world. Anyone that owns a boat and a VHF radio. Both men and women... English speaking. Biggest audience in USA then UK, Australian, NZ, Europe..</p>
      <p>Requirements</p>
    </div>

    <p class="side-column">Sailors, boaters, full time boaters...sailors sailing around the world. Anyone that owns a boat and a VHF radio. Both men and women... English speaking. Biggest audience in USA then UK, Australian, NZ, Europe. Requirements</p>

    <div class="rule rule-bottom"></div>
  </section>

  <main class="cover front">
    <div class="photo-sea" role="img" aria-label="Photograph of a white sailing yacht heeling under full sail on a deep blue sea beneath a bright blue sky"></div>

    <div class="brand">
      <span class="brand-circle"></span>
      <span class="brand-name">Driftwood Kestrel</span>
    </div>

    <div class="band-left"></div>
    <div class="title-panel">
      <h1 class="title">VHF Radio Checklists and Templates for Sailors</h1>
    </div>

    <div class="radio-photo" role="img" aria-label="Photograph of a hand holding a handheld VHF marine radio"></div>

    <h2 class="subtitle">Reducing Mistakes &amp; Making It Easier When Speaking Over The VHF Radio</h2>

    <p class="author">Livia Rose Harrow</p>
  </main>
</body>
</html>
```